Business Cards for new orthopaedic surgery practice

My husband and I are starting our own orthopaedic surgery practice. We are looking for a business card that is uniform, but one will have my name/title and the other will have his. You can just create one design with my name on it for now. But when I choose your design as the winning design I will ask that you add another copy with his name/title.

We are looking for classy, simple, elite all in one. We like dark blues/a little gold/yellow. Something that goes with our logo. We want our logo incorporated. Here is all the info you need:
Business name: RV Bone & Vitality Center
Location: 38517 North Willowmere Ave
Coral Springs, FL 33071
Phone: 954-218-4063
Fax: 954-582-7341
Email: info@myrvbonecare.example

Names: Lydia Vance, M.D.
Board Certified Hand and Upper Extremity Surgeon

Ebo Dansu, M.D.
Board Certified Hip & Knee Replacement/General Orthopaedic Surgeon

Can decide what you want to put on the back. Maybe a slogan:
Rooted in Care. Focused on You

I am just going to upload our logo. The only thing is if we select you as the winning design, the location, and phone numbers may change. We will need your help to update that once fully solidified.

Industry/Entity Type

Medical

Contact Information for Business Card

Colors
0054AA
0677BA
7BADD7
CADEEF
E8F1F8
0094D4
00A9DD
6FCCEA
C7EBF8
E9F6FB

Requirements
Must have
• class, appeal,
Should not have
• We want to air on the side of masculine if we are looking at masculine vs. feminine feel. But we still want it classy, sophisticated, and something we will love

```html
<!DOCTYPE html>
<html lang="en">
<head>
<meta charset="utf-8">
<title>RV Bone &amp; Vitality Center – Business Card</title>
<link rel="stylesheet" href="https://fonts.googleapis.com/css2?family=Cinzel:wght@600&family=Roboto:wght@400&display=swap">
<style>
  :root {
    --backdrop: #e7e8ea;
    --card-white: #f6f6f4;
    --navy: #22399a;
    --sky: #1aa6dc;
    --ink: #3c3d40;
    --edge: #0b8fb8;
  }
  * { box-sizing: border-box; margin: 0; padding: 0; }
  html, body { width: 1200px; height: 884px; overflow: hidden; }
  body {
    background: var(--backdrop);
    font-family: "Roboto", Arial, sans-serif;
    position: relative;
  }
  .card {
    position: absolute;
    left: 280px;
    width: 640px;
    height: 366px;
    border-bottom: 3px solid var(--edge);
    box-shadow: 0 8px 22px rgba(0,0,0,0.12);
    overflow: hidden;
  }
  .card--front { top: 44px; background: var(--card-white); }
  .card--back { top: 474px; background: var(--navy); }

  .brand {
    position: absolute;
    font-family: "Cinzel", Georgia, serif;
    font-weight: 600;
    letter-spacing: 0.04em;
    white-space: nowrap;
  }
  .card--front .brand {
    right: 52px; top: 58px;
    font-size: 21px;
    color: var(--navy);
  }
  .brand-rule {
    position: absolute;
    right: 52px; top: 96px;
    width: 250px; height: 1.5px;
    background: var(--navy);
  }
  .address {
    position: absolute;
    left: 392px; top: 146px;
    font-size: 17px;
    line-height: 24px;
    color: var(--ink);
  }
  .address svg { position: absolute; left: -26px; top: 3px; }

  .person { position: absolute; left: 60px; top: 166px; }
  .person-name {
    font-family: "Cinzel", Georgia, serif;
    font-weight: 600;
    font-size: 21px;
    color: var(--navy);
    letter-spacing: 0.03em;
  }
  .person-title {
    margin-top: 4px;
    font-size: 17px;
    line-height: 22px;
    color: var(--sky);
  }

  .contacts {
    position: absolute;
    left: 186px; top: 250px;
    list-style: none;
    font-size: 17px;
    line-height: 23px;
    color: var(--ink);
  }
  .contacts li { display: flex; align-items: center; gap: 8px; }
  .contacts svg { flex: none; }

  .edge-tab {
    position: absolute;
    left: 0; bottom: 34px;
    width: 44px; height: 18px;
    background: var(--navy);
  }

  .monogram-pattern {
    position: absolute; inset: 0;
    background: linear-gradient(135deg, #2a43a6 0%, #1f3591 55%, #2a43a6 100%);
  }
  .card--back .brand {
    left: 50%; top: 50%;
    transform: translate(-50%, -50%);
    font-size: 24px;
    color: #ffffff;
  }
</style>
</head>
<body>

<section class="card card--front" aria-label="Business card front">
  <div class="brand">RV Bone &amp; Vitality Center</div>
  <div class="brand-rule"></div>

  <address class="address" style="font-style:normal">
    <svg width="16" height="20" viewBox="0 0 16 20" aria-hidden="true">
      <path d="M8 0C3.6 0 0 3.5 0 7.8 0 13.5 8 20 8 20s8-6.5 8-12.2C16 3.5 12.4 0 8 0z" fill="var(--navy)"/>
      <circle cx="8" cy="7.8" r="3" fill="#fff"/>
    </svg>
    38517 North Willowmere Ave,<br>Suite 5 Coral Springs,<br>FL 33071
  </address>

  <div class="person">
    <div class="person-name">LYDIA VANCE, M.D.</div>
    <div class="person-title">Board Certified Hand and<br>Upper Extremity Surgeon</div>
  </div>

  <ul class="contacts">
    <li>
      <svg width="16" height="16" viewBox="0 0 16 16" aria-hidden="true"><path d="M3 1l3 3-2 2c1 2 3 4 5 5l2-2 3 3-2 3C7 15 1 9 1 3z" fill="var(--navy)"/></svg>
      954-218-4063
    </li>
    <li>
      <svg width="16" height="16" viewBox="0 0 16 16" aria-hidden="true"><rect x="1" y="6" width="14" height="8" rx="1" fill="var(--navy)"/><rect x="4" y="1" width="8" height="6" fill="var(--navy)"/><rect x="5" y="2" width="6" height="4" fill="#fff"/></svg>
      954-582-7341
    </li>
    <li>
      <svg width="16" height="16" viewBox="0 0 16 16" aria-hidden="true"><rect x="1" y="3" width="14" height="10" fill="var(--navy)"/><path d="M1 3l7 6 7-6" stroke="#fff" stroke-width="1.2" fill="none"/></svg>
      info@myrvbonecare.example
    </li>
    <li>
      <svg width="16" height="16" viewBox="0 0 16 16" aria-hidden="true"><circle cx="8" cy="8" r="7" fill="var(--navy)"/><path d="M1 8h14M8 1c3 3 3 11 0 14M8 1c-3 3-3 11 0 14" stroke="#fff" stroke-width="1" fill="none"/></svg>
      www.lvancehand.example
    </li>
  </ul>

  <div class="edge-tab"></div>
</section>

<section class="card card--back" aria-label="Business card back">
  <div class="monogram-pattern" role="img" aria-label="Tone-on-tone embossed repeating pattern of the practice mark"></div>
  <div class="brand">RV Bone &amp; Vitality Center</div>
</section>

</body>
</html>
```